Small corporate website template design

I need a couple templates designed for a small corporate website. The corporate site reflects the existence of the parent company which will own various brands/services that have their own websites, so it will mainly be used to present who we are, what we do, what is happening (news/events), how to contact us, link off to our other brand/service sites, as well as post information for public relations, investors, and job opportunities.

The company name is Brelvanto LLC (www.brelvanto-example.com), and the name is representative of stratified layers of interconnected digital services. The corporate site is not expected to generate a bunch of fanfare - that honor will be reserved for the externally linked brand/service sites.

The provided logo may be manipulated in color, size, shape, positioning, etc. to get it to fit with the design, but should be integrated in some way.

What we are looking for is a home page layout as well as a template for an inner page whereby the navigation/logo, etc may be diminished to some extent for the inner pages. We are also interested in reusable elements such as dividers, content containers, etc. in order to represent the types of information described above that we would like to present as described above.

We are particularly interested in consistency of design elements, conservative use of color (including consideration of accessibility concerns), judicious use of whitespace in favor of simplified messaging, and something lending itself well to internationalization/translation.

Target Market(s)

Small business owners, entrepreneurs (B2B)

Number of Pages Required

2 page

Font styles to use
Sans Serif

Requirements
Must have
• See the attached PDF with the logo concept, color swatches, and comparative sites.

```html
<!DOCTYPE html>
<html lang="en">
<head>
<meta charset="utf-8">
<title>Brelvanto LLC</title>
<link rel="stylesheet" href="https://fonts.googleapis.com/css2?family=Montserrat:wght@400;500;600;700&family=Lato:wght@400;700&display=swap">
<style>
:root{
  --orange:#f7941d;
  --orange-deep:#e07a0c;
  --ink:#333333;
  --text:#555555;
  --muted:#777777;
  --peach:#fff5e8;
  --line:#e6e6e6;
  --footer:#333333;
  --white:#ffffff;
}
*{box-sizing:border-box;margin:0;padding:0}
html,body{width:1200px;height:3109px;overflow:hidden;background:var(--white)}
body{position:relative;font-family:'Lato',sans-serif;color:var(--text)}
.abs{position:absolute}
.heading{font-family:'Montserrat',sans-serif;font-weight:600;color:var(--orange)}
.btn{position:absolute;display:flex;align-items:center;justify-content:center;border-radius:24px;
  background:linear-gradient(180deg,var(--orange),var(--orange-deep));color:var(--white);
  font-family:'Montserrat',sans-serif;font-weight:700;font-size:20px;letter-spacing:.5px}

/* header */
.brand{left:79px;top:36px;display:flex;align-items:center;gap:10px;font-family:'Montserrat',sans-serif;font-weight:700;font-size:22px;color:var(--orange)}
.brand-dot{width:22px;height:22px;border-radius:50%;background:var(--orange)}
.nav{top:41px;left:0;font-family:'Montserrat',sans-serif;font-size:15.5px;color:var(--ink)}
.nav span{position:absolute;white-space:nowrap}
.nav .active{color:var(--orange)}

/* hero */
.hero-title{left:75px;top:300px;font-size:45px;font-weight:700}
.hero-sub{left:79px;top:372px;font-size:24px;line-height:35px;color:var(--ink);width:420px}

/* services */
.service{width:360px;text-align:center}
.service svg{display:block;margin:0 auto}
.service h3{margin-top:22px;font-family:'Montserrat',sans-serif;font-weight:500;font-size:19.5px;color:var(--ink);white-space:nowrap}
.service .rule{width:32px;height:3px;background:var(--orange);margin:14px auto 20px}
.service p{width:296px;margin:0 auto;font-size:15px;line-height:25px;color:var(--text)}

/* welcome */
.welcome-kicker{left:605px;top:1162px;font-size:31px;font-weight:700}
.welcome-title{left:605px;top:1202px;font-size:41px;font-weight:700}
.welcome-text{left:607px;top:1266px;width:520px;font-size:15.5px;line-height:25px;color:var(--text)}

/* news */
.section-title{width:1200px;left:0;text-align:center;font-size:41px;font-weight:700}
.card{position:absolute;background:var(--white);box-shadow:0 2px 8px rgba(0,0,0,.12);border-radius:3px}
.news-card{width:323px;height:331px;top:1688px;border-top:4px solid var(--orange);padding:28px 13px 0 13px}
.news-meta{display:flex;justify-content:space-between;font-size:15.5px;color:var(--ink)}
.news-card h4{margin-top:24px;font-family:'Lato',sans-serif;font-weight:700;font-size:21.5px;line-height:33px;color:var(--ink)}
.news-card p{margin-top:12px;width:286px;font-size:15px;line-height:25px;color:var(--text)}
.news-link{display:inline-block;margin-top:12px;font-size:15px;color:var(--ink);text-decoration:underline}

/* testimonials */
.testi-title{left:79px;top:2294px;font-size:41px;font-weight:700}
.quote-card{width:323px;height:207px;top:2378px;padding:28px 14px 0;text-align:center}
.quote-card p{font-size:15px;line-height:25px;color:var(--text)}
.quote-card .client{margin-top:10px;font-size:14.5px;color:var(--ink)}
.slider-dots{left:79px;top:2626px;display:flex;gap:8px}
.slider-dots i{display:block;width:32px;height:3px;background:var(--line)}
.slider-dots i.on{background:var(--orange)}

/* subscribe */
.sub-title{top:2738px}
.sub-text{left:270px;width:660px;top:2804px;text-align:center;font-size:15.5px;line-height:25px;color:var(--text)}
.email{left:286px;top:2884px;width:440px;height:44px;border:1px solid var(--line);border-radius:22px;
  box-shadow:0 1px 4px rgba(0,0,0,.1);padding-left:24px;display:flex;align-items:center;font-size:15px;color:#999}

/* footer */
.footer{left:0;top:2993px;width:1200px;height:116px;background:var(--footer);color:var(--white);font-size:15.5px}
.footer-nav span{position:absolute;top:26px}
.copy{position:absolute;top:72px;width:100%;text-align:center;font-size:15px}
</style>
</head>
<body>

<header>
  <div class="abs brand"><span class="brand-dot"></span>Brelvanto LLC</div>
  <nav class="abs nav">
    <span class="active" style="left:379px">HOME</span>
    <span style="left:464px">ABOUT</span>
    <span style="left:555px">SERVICES</span>
    <span style="left:662px">NEWS</span>
    <span style="left:745px">CONTACT</span>
  </nav>
</header>

<section class="hero">
  <svg class="abs" style="left:0;top:0" width="1200" height="640" role="img" aria-label="Photo of two colleagues smiling at a laptop in an office">
    <defs>
      <linearGradient id="heroGrad" x1="0" y1="0" x2="1" y2="1">
        <stop offset="0" stop-color="#e9ecef"/>
        <stop offset=".55" stop-color="#c9ced3"/>
        <stop offset="1" stop-color="#8f8a86"/>
      </linearGradient>
    </defs>
    <path d="M620,118 L1200,62 L1200,500 L735,618 Q690,628 668,590 L490,235 Q462,150 540,128 Z" fill="url(#heroGrad)"/>
  </svg>
  <h1 class="abs heading hero-title">Brelvanto LLC</h1>
  <p class="abs hero-sub">Adaptive Software Technology for the Digital Revolution</p>
  <a class="btn" style="left:79px;top:460px;width:176px;height:48px">CONTACT US</a>
</section>

<section class="services">
  <div class="abs service" style="left:60px;top:700px">
    <svg width="70" height="70" viewBox="0 0 70 70"><circle cx="33" cy="37" r="28" fill="none" stroke="#f7941d" stroke-width="6"/><circle cx="33" cy="37" r="16" fill="none" stroke="#f7941d" stroke-width="6"/><circle cx="33" cy="37" r="5" fill="#f7941d"/><path d="M33,37 L60,10 M52,8 L62,8 L62,18" stroke="#f7941d" stroke-width="5" fill="none"/></svg>
    <h3>Marketing Strategy</h3><div class="rule"></div>
    <p>Lorem Ipsum is simply dummy text of the printing and typesetting industry. Lorem Ipsum has been the industry's standard.</p>
  </div>
  <div class="abs service" style="left:418px;top:700px">
    <svg width="84" height="70" viewBox="0 0 84 70"><rect x="6" y="10" width="46" height="34" fill="none" stroke="#f7941d" stroke-width="4"/><rect x="2" y="46" width="58" height="6" fill="#f7941d"/><circle cx="56" cy="22" r="14" fill="none" stroke="#e07a0c" stroke-width="5"/><path d="M66,32 L80,46" stroke="#e07a0c" stroke-width="6"/></svg>
    <h3>Digital Analytics</h3><div class="rule"></div>
    <p>Lorem Ipsum is simply dummy text of the printing and typesetting industry. Lorem Ipsum has been the industry's standard.</p>
  </div>
  <div class="abs service" style="left:780px;top:700px">
    <svg width="70" height="70" viewBox="0 0 70 70"><circle cx="42" cy="24" r="16" fill="none" stroke="#f7941d" stroke-width="7" stroke-dasharray="6 4"/><circle cx="42" cy="24" r="7" fill="#f7941d"/><circle cx="20" cy="50" r="12" fill="none" stroke="#e07a0c" stroke-width="6" stroke-dasharray="5 3"/><circle cx="20" cy="50" r="4" fill="#e07a0c"/></svg>
    <h3>Management and Optimization</h3><div class="rule"></div>
    <p>Lorem Ipsum is simply dummy text of the printing and typesetting industry. Lorem Ipsum has been the industry's standard.</p>
  </div>
</section>

<section class="welcome">
  <svg class="abs" style="left:0;top:960px" width="640" height="620">
    <path d="M0,14 C200,40 470,100 560,150 Q622,190 610,300 L585,500 Q565,605 470,605 L0,605 Z" fill="var(--peach)"/>
  </svg>
  <svg class="abs" style="left:0;top:1138px" width="530" height="335" role="img" aria-label="Laptop displaying an analytics dashboard">
    <defs>
      <linearGradient id="laptopGrad" x1="0" y1="0" x2="1" y2="1">
        <stop offset="0" stop-color="#e4e7ea"/>
        <stop offset="1" stop-color="#b9bcbf"/>
      </linearGradient>
    </defs>
    <rect x="0" y="0" width="530" height="335" rx="10" fill="url(#laptopGrad)"/>
  </svg>
  <p class="abs heading welcome-kicker">Welcome to</p>
  <h2 class="abs heading welcome-title">Brelvanto LLC</h2>
  <p class="abs welcome-text">Lorem Ipsum is simply dummy text of the printing and typesetting industry. Lorem Ipsum has been the industry's standard dummy text ever since the 1500s, when an unknown printer took a galley of type and scrambled.</p>
  <a class="btn" style="left:603px;top:1358px;width:176px;height:46px">READ MORE</a>
</section>

<section class="news">
  <h2 class="abs heading section-title" style="top:1616px">Latest News</h2>
  <article class="card news-card" style="left:77px">
    <div class="news-meta"><span>27 May 2018</span><span>Jhon Doe</span></div>
    <h4>Lorem Ipsum is simply dummy text of the printing .</h4>
    <p>Lorem Ipsum is simply dummy text of the printing and typesetting industry. Lorem Ipsum has been the industry's standard dummy text ever since the 1500s.</p>
    <a class="news-link">READ MORE...</a>
  </article>
  <article class="card news-card" style="left:437px">
    <div class="news-meta"><span>27 May 2018</span><span>Jhon Doe</span></div>
    <h4>Lorem Ipsum is simply dummy text of the printing .</h4>
    <p>Lorem Ipsum is simply dummy text of the printing and typesetting industry. Lorem Ipsum has been the industry's standard dummy text ever since the 1500s.</p>
    <a class="news-link">READ MORE...</a>
  </article>
  <article class="card news-card" style="left:798px">
    <div class="news-meta"><span>27 May 2018</span><span>Jhon Doe</span></div>
    <h4>Lorem Ipsum is simply dummy text of the printing .</h4>
    <p>Lorem Ipsum is simply dummy text of the printing and typesetting industry. Lorem Ipsum has been the industry's standard dummy text ever since the 1500s.</p>
    <a class="news-link">READ MORE...</a>
  </article>
</section>

<section class="testimonials">
  <svg class="abs" style="left:600px;top:2070px" width="600" height="600" role="img" aria-label="Photo of hands typing on a laptop at a bright white desk">
    <defs>
      <linearGradient id="testiGrad" x1="0" y1="0" x2="1" y2="1">
        <stop offset="0" stop-color="#f3f3f3"/>
        <stop offset=".5" stop-color="#e4dcd8"/>
        <stop offset="1" stop-color="#9a9a9a"/>
      </linearGradient>
    </defs>
    <path d="M100,100 L600,13 L600,520 L230,583 Q180,590 160,540 L40,220 Q25,130 100,100 Z" fill="url(#testiGrad)"/>
  </svg>
  <h2 class="abs heading testi-title">Testimonials</h2>
  <blockquote class="card quote-card" style="left:77px">
    <p>"Lorem Ipsum is simply dummy text of the printing and typesetting industry. Lorem Ipsum has been the industry's standard dummy text ever since the 1500s."</p>
    <p class="client">- CLIENT NAME</p>
  </blockquote>
  <blockquote class="card quote-card" style="left:430px">
    <p>"Lorem Ipsum is simply dummy text of the printing and typesetting industry. Lorem Ipsum has been the industry's standard dummy text ever since the 1500s."</p>
    <p class="client">- CLIENT NAME</p>
  </blockquote>
  <div class="abs slider-dots"><i class="on"></i><i></i><i></i></div>
</section>

<section class="subscribe">
  <h2 class="abs heading section-title sub-title">Subscribe to Our News Letter</h2>
  <p class="abs sub-text">Lorem Ipsum is simply dummy text of the printing and typesetting industry. Lorem Ipsum has been the industry's standard dummy text ever since the 1500s.</p>
  <div class="abs email">Enter your email address</div>
  <a class="btn" style="left:736px;top:2884px;width:176px;height:44px">SUBSCRIBE</a>
</section>

<footer class="abs footer">
  <nav class="footer-nav">
    <span style="left:384px">Home</span>
    <span style="left:474px">About</span>
    <span style="left:564px">Services</span>
    <span style="left:668px">News</span>
    <span style="left:757px">Contact</span>
  </nav>
  <p class="copy">©Brelvanto LLC,  2018. All Rights Reserved.</p>
</footer>

</body>
</html>
```